Business card por a urban DJ, up scale audience target

Need a sober design, modern, conservative colors but i can consider some options, y play rnb, hip hop, EDM and top40.

Business card for contact and personal info, double sided, use logo attrached please; im 42 so i need a card acording to my age an target audience.

Target Market(s)

Adult people, up scale audience

Industry/Entity Type

Music Download

Contact Information for Business Card

Cel (318) 4207265518 www.lumadrift.com

Requirements
Must have
• open mind
Nice to have
• open mind
Should not have
• DJ

```html
<!DOCTYPE html>
<html lang="en">
<head>
<meta charset="utf-8">
<title>Luma Drift Business Card</title>
<link rel="stylesheet" href="https://fonts.googleapis.com/css2?family=Open+Sans:wght@400;600;700&display=swap">
<style>
  :root {
    --page-bg: #e9e7e4;
    --card-light: #ffffff;
    --card-dark: #2b2b2b;
    --ink-dark: #2b2b2b;
    --ink-light: #d4d4d6;
    --text-light: #f2f2f2;
    --name-tone: #c8c3c7;
  }
  * { box-sizing: border-box; margin: 0; padding: 0; }
  html, body {
    width: 1200px;
    height: 900px;
    overflow: hidden;
    background: var(--page-bg);
    font-family: "Open Sans", sans-serif;
  }
  .canvas {
    width: 1200px;
    height: 900px;
    display: flex;
    align-items: center;
    justify-content: center;
    gap: 40px;
  }
  .card {
    width: 540px;
    height: 309px;
    position: relative;
    box-shadow: 0 6px 18px rgba(0,0,0,0.18);
  }
  .card--front {
    background: var(--card-light);
    display: flex;
    align-items: center;
    justify-content: center;
  }
  .card--back {
    background: var(--card-dark);
    color: var(--text-light);
  }
  .brand-name {
    font-family: "Open Sans", sans-serif;
    font-weight: 700;
    letter-spacing: 2px;
    line-height: 1;
    white-space: nowrap;
  }
  .card--front .brand-name {
    color: var(--ink-dark);
    font-size: 52px;
  }
  .card--back .brand-name {
    position: absolute;
    left: 40px;
    top: 128px;
    color: var(--ink-light);
    font-size: 40px;
  }
  .contact {
    position: absolute;
    left: 330px;
    top: 88px;
    font-size: 12.5px;
    line-height: 1.35;
  }
  .contact__name {
    font-weight: 600;
    font-size: 16px;
    color: var(--name-tone);
  }
  .contact__role { margin-bottom: 12px; }
  .contact__address { margin-bottom: 10px; margin-left: 14px; }
  .contact__list { list-style: none; margin-left: 26px; }
  .contact__item {
    display: flex;
    align-items: center;
    gap: 10px;
  }
  .contact__icon { width: 10px; height: 10px; fill: var(--text-light); flex: none; }
</style>
</head>
<body>
<main class="canvas">
  <section class="card card--front" aria-label="Card front">
    <span class="brand-name">LUMA DRIFT</span>
  </section>

  <section class="card card--back" aria-label="Card back">
    <span class="brand-name">LUMA DRIFT</span>
    <div class="contact">
      <p class="contact__name">Marcus Hale</p>
      <p class="contact__role">Managing Director</p>
      <p class="contact__address">12345, Address Goes Here<br>Country Name, 123456.</p>
      <ul class="contact__list">
        <li class="contact__item">
          <svg class="contact__icon" viewBox="0 0 10 10" aria-hidden="true"><path d="M2 0.5 L3.6 2.6 L2.7 3.6 Q3.8 5.9 6.4 7.3 L7.4 6.4 L9.5 8 L8.3 9.5 Q1 8 0.5 1.7 Z"/></svg>
          <span>(318) 4207265518</span>
        </li>
        <li class="contact__item">
          <svg class="contact__icon" viewBox="0 0 10 10" aria-hidden="true"><path d="M0.5 2 H9.5 V8.5 H0.5 Z M1.3 2.6 L5 5.6 L8.7 2.6" fill="none" stroke="#f2f2f2" stroke-width="1"/></svg>
          <span>info@lumadrift.com</span>
        </li>
        <li class="contact__item">
          <svg class="contact__icon" viewBox="0 0 10 10" aria-hidden="true"><path d="M4 6 L6 4 M3.2 5.2 L1.6 6.8 A1.3 1.3 0 0 0 3.2 8.4 L4.8 6.8 M6.8 4.8 L8.4 3.2 A1.3 1.3 0 0 0 6.8 1.6 L5.2 3.2" fill="none" stroke="#f2f2f2" stroke-width="1.1" stroke-linecap="round"/></svg>
          <span>www.lumadrift.com</span>
        </li>
      </ul>
    </div>
  </section>
</main>
</body>
</html>
```